New, modern business card for growing audiology practice

We need a new business card for our audiology practice. Our logo and website have recently changed (more modern) and we want our business cards to reflect this change.
We conduct hearing tests, perform earwax removals, and fit & dispense hearing aids to our patients. We are a family owned practice in which the owner is the one who works directly with the patient. I have attached logos in various formats to use, as well as two ideas I found on this website; as well as a scanned copy of our current logo. Good luck!

Industry/Entity Type

Business

Contact Information for Business Card

Company name: Tolvera Hearing Center
Provider name: Peter Wolstenby, Au.D. F/NSB
Phone number: (555) 683-5127
Address: 837 W. Lindell Ave. Brenlow Falls, OH 44710
email: tolverahearing@postvane.com
website: tolverahearing.com

Colors
000000
aaaaaa
dbdbdb
cacaca
9bcb3c
afd23c
cadf82
b1b1b1

Requirements
Must have
• My card must include information in the "details" section. In the attached images, I found a few that I liked and I would like to model after - "brisky bouncin'" and "Sound Method Center".
• Must be horizontal.
• Must include logos provided. I uploaded them in various file formats and various ways.
• Must match logo font, if possible, if not, please get as close as you can.
Nice to have
• I really like the idea of having a color on one side with just the logo and company name and the contact information and provider name on the other side. I also really like the idea of having the main color dominating on the logo/company side with accent of that same color on the contact side of the card.
Should not have
• Must not be vertical.

```html
<!DOCTYPE html>
<html lang="en">
<head>
<meta charset="utf-8">
<title>Tolvera Hearing Center — Business Card</title>
<link rel="stylesheet" href="https://fonts.googleapis.com/css2?family=Questrial&family=Roboto:wght@400;500&family=Saira+Condensed:wght@600&display=swap">
<style>
  :root {
    --backdrop: #3a3a3a;
    --card: #1c1c1c;
    --green: #609c38;
    --green-light: #6fae3f;
    --grey-band: #b1b1b1;
    --white: #f4f4f4;
    --muted: #8a8a8a;
  }
  * { margin: 0; padding: 0; box-sizing: border-box; }
  html, body { width: 799px; height: 1200px; overflow: hidden; }
  body {
    background: var(--backdrop);
    display: flex;
    flex-direction: column;
    align-items: center;
    justify-content: center;
    gap: 130px;
    font-family: "Roboto", Arial, sans-serif;
  }
  .card {
    position: relative;
    width: 640px;
    height: 366px;
    background: var(--card);
    overflow: hidden;
    box-shadow: 0 10px 24px rgba(0,0,0,.45);
  }
  /* front */
  .card-front {
    display: flex;
    align-items: center;
    justify-content: center;
    gap: 16px;
  }
  .brand-dot {
    width: 26px; height: 26px;
    border-radius: 50%;
    background: var(--muted);
    flex: none;
  }
  .brand-name-front {
    font-family: "Questrial", Arial, sans-serif;
    font-size: 34px;
    letter-spacing: 1px;
    text-transform: uppercase;
    color: var(--muted);
  }
  /* back */
  .brand-row {
    position: absolute;
    top: 34px; left: 38px;
    display: flex;
    align-items: center;
    gap: 14px;
  }
  .brand-row .brand-dot { width: 30px; height: 30px; background: var(--green-light); }
  .brand-name {
    font-family: "Questrial", Arial, sans-serif;
    font-size: 38px;
    letter-spacing: .5px;
    text-transform: uppercase;
    color: var(--white);
    white-space: nowrap;
  }
  .provider { position: absolute; top: 136px; left: 38px; width: 290px; }
  .provider-name {
    font-family: "Saira Condensed", "Arial Narrow", sans-serif;
    font-weight: 600;
    font-size: 23px;
    line-height: 26px;
    color: var(--green-light);
    white-space: nowrap;
  }
  .provider-role { font-size: 13px; color: var(--white); margin-top: 2px; }
  .contact {
    position: absolute;
    top: 176px; left: 350px;
    font-size: 15px;
    line-height: 21px;
    color: var(--white);
    list-style: none;
  }
  .contact li { display: flex; align-items: center; gap: 10px; white-space: nowrap; }
  .contact .indent { padding-left: 26px; }
  .contact svg { width: 16px; height: 16px; fill: var(--green-light); flex: none; }
  .bands { position: absolute; left: 0; top: 0; width: 640px; height: 366px; }
  .website {
    position: absolute;
    right: 0; bottom: 0;
    width: 400px; height: 88px;
    display: flex; align-items: center; justify-content: center;
    font-size: 18px;
    color: var(--white);
  }
</style>
</head>
<body>
  <section class="card card-front" aria-label="Card front">
    <span class="brand-dot"></span>
    <span class="brand-name-front">Tolvera Hearing Center</span>
  </section>

  <section class="card card-back" aria-label="Card back">
    <svg class="bands" viewBox="0 0 640 366" aria-hidden="true">
      <rect x="0" y="262" width="260" height="18" fill="var(--grey-band)"/>
      <polygon points="262,278 640,278 640,366 205,366" fill="var(--green)"/>
    </svg>

    <div class="brand-row">
      <span class="brand-dot"></span>
      <span class="brand-name">Tolvera Hearing Center</span>
    </div>

    <div class="provider">
      <p class="provider-name">Peter Wolstenby, Au.D. F/NSB</p>
      <p class="provider-role">Owner - Audiologist</p>
    </div>

    <ul class="contact">
      <li class="indent">837 W. Lindell Ave.</li>
      <li class="indent">Brenlow Falls, OH 44710</li>
      <li>
        <svg viewBox="0 0 16 16"><path d="M3 2h3l1.5 3.5-2 1.2a8 8 0 0 0 3.8 3.8l1.2-2L14 10v3c0 .6-.4 1-1 1A11 11 0 0 1 2 3c0-.6.4-1 1-1z"/></svg>
        (555) 683-5127
      </li>
      <li>
        <svg viewBox="0 0 16 16"><path d="M1 3h14v10H1zM2 4.2v.5l6 4 6-4v-.5z"/></svg>
        tolverahearing@postvane.com
      </li>
    </ul>

    <p class="website">www.tolverahearing.com</p>
  </section>
</body>
</html>
```